Building Referrer Relationships Booklet

4 page A4 booklet to give to potential professional referrers to establish a collaborative relationship.Needs to be bright, vibrant, colourful, friendly, inviting, in keeping with The Linden Practice colours.
Want to provide potential referrer partners a great reason to choose to collaborate with us. They need to know who we are, what makes us different/appealing, and who we are looking for to connect with.
The final product should communicate high performance and connectedness.
Updates

Target Market(s)

professional medical allied health and fitness practitioners

Industry/Entity Type

Health

Requirements
Must have
• energetic, vibrant, engaging, inviting, images

```html
<!DOCTYPE html>
<html lang="en">
<head>
<meta charset="utf-8">
<title>Referral Partnerships Booklet</title>
<link href="https://fonts.googleapis.com/css2?family=Open+Sans:wght@400;600;700;800&display=swap" rel="stylesheet">
<style>
:root{
  --bg:#eef0f2;
  --blue:#1d63b0;
  --navy:#123a70;
  --orange:#f28a22;
  --teal:#19a7c9;
  --green:#7bbf3a;
  --ink:#3a4350;
  --muted:#6f7986;
  --paper:#ffffff;
  --tint:#eaf3fb;
}
*{box-sizing:border-box;margin:0;padding:0}
html,body{width:882px;height:1200px;overflow:hidden;background:var(--bg);font-family:"Open Sans",Arial,sans-serif;color:var(--ink)}
.spread{position:absolute;left:31px;width:820px;height:580px;background:var(--paper);display:flex;box-shadow:0 2px 8px rgba(0,0,0,.15)}
.spread.outer{top:14px}
.spread.inner{top:606px}
.page{position:relative;width:410px;height:580px;overflow:hidden}
.page+.page{border-left:1px solid #e3e6ea}

/* photo areas: soft gradients in the photos' main tones */
.photo-hands{background:linear-gradient(160deg,#e9eef4 0%,#d9c2a9 35%,#c79a78 60%,#8fb3d6 100%)}
.photo-team{background:linear-gradient(120deg,#8cc0e6 0%,#f2d3b8 40%,#d99b6c 65%,#4f8bc4 100%)}
.photo-treat{background:linear-gradient(135deg,#f4d9c2,#e09a6a 55%,#2f6fb5)}
.photo-portrait{background:linear-gradient(180deg,#e7eef6 0%,#e8c4a4 55%,#5d86b8 100%)}

/* back cover */
.info-bar{position:absolute;top:0;left:0;right:0;height:128px;background:var(--orange);display:flex;gap:16px;padding:12px 18px;color:#fff}
.info-col{flex:1;font-size:6.5px;line-height:1.75}
.info-col h4{font-size:7.5px;font-weight:700;margin-bottom:3px}
.pathways-title{position:absolute;top:140px;width:100%;text-align:center;color:var(--orange);font-weight:800;font-size:9px;letter-spacing:.5px}
.pathways{position:absolute;top:160px;left:20px;right:20px;list-style:none}
.pathways li{display:flex;gap:8px;margin-bottom:11px;font-size:6.5px;line-height:1.5}
.pathways .num{flex:0 0 18px;height:18px;border-radius:50%;background:var(--blue);color:#fff;font-weight:700;font-size:8px;display:flex;align-items:center;justify-content:center}
.pathways b{color:var(--blue);font-size:7.5px;display:block}
.badges{position:absolute;top:420px;left:20px;right:20px;display:flex;justify-content:space-between}
.badge{width:44px;height:18px;background:#d9dde3;border-radius:3px}
.contact-banner{position:absolute;top:456px;left:0;right:0;text-align:center}
.contact-banner h3{display:inline-block;background:var(--blue);color:#fff;font-size:10px;font-weight:800;padding:5px 28px;border-radius:3px}
.contact-banner p{font-size:6.5px;margin-top:6px}
.foot-strip{position:absolute;bottom:0;left:0;right:0;height:22px;background:var(--orange);color:#fff;font-size:6.5px;display:flex;justify-content:space-around;align-items:center;font-weight:600}

/* front cover */
.cover-title{position:absolute;top:30px;width:100%;text-align:center}
.cover-title h1{color:var(--blue);font-size:20px;font-weight:800;letter-spacing:.5px}
.cover-title p{color:var(--navy);font-size:13px;margin-top:2px}
.cover-photo{position:absolute;top:100px;left:0;right:0;height:330px}
.cover-wave{position:absolute;left:0;top:380px;width:410px;height:180px}
.brand{position:absolute;top:470px;left:22px;display:flex;align-items:center;gap:6px;color:#fff;font-weight:700;font-size:9px}
.brand i{width:12px;height:12px;border-radius:50%;background:#fff;display:block}
.cover-msg{position:absolute;top:468px;right:18px;width:220px;color:#fff;font-size:7px;line-height:1.5;text-align:right}

/* inner left */
.values{position:absolute;top:22px;left:20px;font-size:9px;font-weight:800;letter-spacing:.3px}
.values .o{color:var(--orange)}.values .b{color:var(--blue)}.values .t{color:var(--teal)}.values .g{color:var(--green)}
.intro{position:absolute;top:46px;left:20px;width:370px;font-size:6.8px;line-height:1.6}
.intro p{margin-bottom:5px}
.intro .hl{color:var(--orange);font-weight:700}
.strap{position:absolute;top:166px;left:0;right:0;padding:8px 20px;background:var(--tint);border-left:4px solid var(--orange);font-size:7.5px;color:var(--blue);font-weight:700}
.looking{position:absolute;top:204px;left:20px;width:172px}
.looking h4{background:var(--blue);color:#fff;font-size:7.5px;font-weight:700;padding:6px 8px;border-radius:3px;margin-bottom:10px;line-height:1.35}
.looking ol{list-style:none}
.looking li{display:flex;gap:7px;font-size:6.5px;line-height:1.5;margin-bottom:13px}
.looking .num{flex:0 0 15px;height:15px;border-radius:50%;background:var(--orange);color:#fff;font-weight:700;font-size:7px;display:flex;align-items:center;justify-content:center}
.closing{position:absolute;top:430px;left:20px;width:172px;font-size:6.5px;line-height:1.6}
.closing h4{color:var(--orange);font-size:7.5px;margin-bottom:4px}
.team{position:absolute;top:204px;left:206px;width:184px}
.team h4{color:var(--blue);font-size:7.5px;font-weight:700;text-align:center;margin-bottom:8px}
.team-grid{display:grid;grid-template-columns:repeat(3,1fr);gap:10px 8px}
.member .pic{height:70px;border-radius:3px}
.member span{display:block;font-size:5.5px;text-align:center;margin-top:3px;color:var(--muted)}
.left-band{position:absolute;bottom:0;left:0;right:0;height:10px;background:linear-gradient(90deg,var(--orange),var(--blue) 50%,var(--teal))}

/* inner right */
.team-photo{position:absolute;top:14px;left:14px;width:382px;height:160px}
.round-photo{position:absolute;top:132px;right:20px;width:66px;height:66px;border-radius:50%;border:3px solid #fff}
.diff{position:absolute;top:184px;left:20px;width:370px}
.diff h3{color:var(--orange);font-size:8.5px;font-weight:800;margin-bottom:2px}
.diff .sub{font-size:6.5px;margin-bottom:12px}
.diff ul{list-style:none}
.diff li{display:flex;gap:9px;font-size:6.5px;line-height:1.5;margin-bottom:14px}
.diff .ico{flex:0 0 20px;height:20px;border-radius:50%;background:var(--blue);display:flex;align-items:center;justify-content:center}
.diff b{color:var(--blue);display:block;font-size:7.5px}
.request{position:absolute;bottom:10px;left:0;right:0;background:var(--blue);padding:7px 20px;border-top:3px solid var(--orange);font-size:7.5px;color:#fff;font-weight:700}
</style>
</head>
<body>

<section class="spread outer">
  <article class="page back-cover">
    <div class="info-bar">
      <div class="info-col">
        <h4>Our Clinic Information</h4>
        • Open six days with early starts<br>• Late sessions on weekday nights<br>• On-site parking and easy access<br>• Same-week bookings for referrals<br>• Clear reports sent after each visit<br>• Health fund rebates on the spot
      </div>
      <div class="info-col">
        <h4>Our Referral Services</h4>
        • Podiatry and foot care<br>• Sports injury assessment<br>• Custom orthotic therapy<br>• Gait and running analysis<br>• Diabetic foot screening<br>• Children's foot health
      </div>
    </div>
    <div class="pathways-title">REFERRAL PATHWAYS</div>
    <ol class="pathways">
      <li><span class="num">1</span><div><b>Massage Therapists</b>Share clients with foot or lower limb pain for a joint plan of care.</div></li>
      <li><span class="num">2</span><div><b>Clinical Pilates</b>We align rehab goals so clients move well and stay on track.</div></li>
      <li><span class="num">3</span><div><b>Personal Trainers</b>Refer clients with recurring pain for a fast, clear assessment.</div></li>
      <li><span class="num">4</span><div><b>GP Health Teams</b>Care plan referrals welcomed with reports back to your team.</div></li>
      <li><span class="num">5</span><div><b>Orthopaedic Surgeons</b>Pre and post surgery foot care, shared notes and updates.</div></li>
      <li><span class="num">6</span><div><b>Physiotherapists</b>Two-way referrals for complex lower limb and gait issues.</div></li>
      <li><span class="num">7</span><div><b>Sports Clubs</b>Screening days and injury care for players and coaches.</div></li>
    </ol>
    <div class="badges">
      <span class="badge"></span><span class="badge"></span><span class="badge"></span><span class="badge"></span><span class="badge"></span><span class="badge"></span>
    </div>
    <div class="contact-banner">
      <h3>CONTACT US</h3>
      <p>Collective Contact: 48 Orchard Lane, Brookvale — call us to set up a referral chat</p>
    </div>
    <div class="foot-strip"><span>(03) 5550 2140</span><span>hello@lindenpractice.example</span><span>www.lindenpractice.example</span></div>
  </article>

  <article class="page front-cover">
    <div class="cover-title">
      <h1>REFERRAL PARTNERSHIPS</h1>
      <p>Because Together We Achieve</p>
    </div>
    <div class="cover-photo photo-hands" role="img" aria-label="Team members stacking hands together in a circle against a bright sky"></div>
    <svg class="cover-wave" viewBox="0 0 410 180" preserveAspectRatio="none" aria-hidden="true">
      <path d="M0 50 Q205 0 410 40 L410 180 L0 180Z" fill="var(--teal)"/>
      <path d="M0 62 Q205 18 410 54 L410 180 L0 180Z" fill="var(--blue)"/>
    </svg>
    <div class="brand"><i></i>The Linden Practice</div>
    <div class="cover-msg">We are here to help our clients get back on their feet.<br>Let's combine our brilliance so we can achieve even better results.</div>
    <div class="foot-strip"><span>(03) 5550 2140</span><span>hello@lindenpractice.example</span><span>www.lindenpractice.example</span></div>
  </article>
</section>

<section class="spread inner">
  <article class="page about">
    <div class="values"><span class="o">LEARNING</span> • <span class="b">INSPIRATION</span> • <span class="t">FUN</span> • <span class="g">CREATIVE</span> • <span class="o">WORK</span> • <span class="b">TEAM</span></div>
    <div class="intro">
      <p><span class="hl">Our vision</span> is to be a trusted leader in foot health, known across the region for care that gets people moving again and keeps them active for life.</p>
      <p><span class="hl">Our mission</span> is to deliver clear, caring and proven treatment for every client who walks in our door, from first steps to elite sport.</p>
      <p><span class="hl">We believe</span> great results come from great teams, so we work closely with the people around our clients and share what we learn.</p>
      <p><span class="hl">Our values</span> guide each visit: listen first, explain clearly, treat well and always follow up with you and your client.</p>
    </div>
    <div class="strap">At The Linden Practice, we are passionate about building strong referral partnerships.</div>
    <div class="looking">
      <h4>Who we are looking for to partner with:</h4>
      <ol>
        <li><span class="num">1</span><span>Practitioners who put client outcomes first and value shared care plans across disciplines.</span></li>
        <li><span class="num">2</span><span>Teams who enjoy clear, quick communication and regular progress updates.</span></li>
        <li><span class="num">3</span><span>Clinics and coaches who want a reliable partner for foot and lower limb care.</span></li>
      </ol>
    </div>
    <div class="team">
      <h4>Our Team</h4>
      <div class="team-grid">
        <div class="member"><div class="pic photo-portrait" role="img" aria-label="Portrait of podiatrist"></div><span>A. Hart</span></div>
        <div class="member"><div class="pic photo-portrait" role="img" aria-label="Portrait of podiatrist"></div><span>B. Cole</span></div>
        <div class="member"><div class="pic photo-portrait" role="img" aria-label="Portrait of podiatrist"></div><span>C. Reyes</span></div>
        <div class="member"><div class="pic photo-portrait" role="img" aria-label="Portrait of podiatrist"></div><span>D. Marsh</span></div>
        <div class="member"><div class="pic photo-portrait" role="img" aria-label="Portrait of practice manager"></div><span>E. Quinn</span></div>
        <div class="member"><div class="pic photo-portrait" role="img" aria-label="Portrait of reception lead"></div><span>F. Lowe</span></div>
      </div>
    </div>
    <div class="closing">
      <h4>Why partner with us?</h4>
      Our referral partners get fast booking, prompt written reports and a team that treats their clients as our own. Together we help people move better, recover sooner and stay active in the things they love.
    </div>
    <div class="left-band"></div>
  </article>

  <article class="page difference">
    <div class="team-photo photo-team" role="img" aria-label="Group photo of the clinic team smiling together outdoors"></div>
    <div class="round-photo photo-treat" role="img" aria-label="Practitioner treating a client's foot"></div>
    <div class="diff">
      <h3>OUR POINT OF DIFFERENCE</h3>
      <p class="sub">What makes The Linden Practice a great referral partner</p>
      <ul>
        <li><span class="ico"><svg width="10" height="10" viewBox="0 0 10 10"><path d="M1.5 5.2 4 7.5 8.5 2.5" stroke="#fff" stroke-width="1.6" fill="none"/></svg></span><div><b>Fast Access</b>Referred clients are seen within the week, often within two days of your call.</div></li>
        <li><span class="ico"><svg width="10" height="10" viewBox="0 0 10 10"><path d="M1.5 5.2 4 7.5 8.5 2.5" stroke="#fff" stroke-width="1.6" fill="none"/></svg></span><div><b>Clear Reports</b>Short written updates sent back to you after each key visit and review.</div></li>
        <li><span class="ico"><svg width="10" height="10" viewBox="0 0 10 10"><path d="M1.5 5.2 4 7.5 8.5 2.5" stroke="#fff" stroke-width="1.6" fill="none"/></svg></span><div><b>Modern Tools</b>Gait analysis and digital scanning for precise, comfortable orthotic care.</div></li>
        <li><span class="ico"><svg width="10" height="10" viewBox="0 0 10 10"><path d="M1.5 5.2 4 7.5 8.5 2.5" stroke="#fff" stroke-width="1.6" fill="none"/></svg></span><div><b>Shared Goals</b>We build plans that support the work you are already doing with your client.</div></li>
        <li><span class="ico"><svg width="10" height="10" viewBox="0 0 10 10"><path d="M1.5 5.2 4 7.5 8.5 2.5" stroke="#fff" stroke-width="1.6" fill="none"/></svg></span><div><b>Ongoing Learning</b>Our team trains often and shares new ideas and research with partners.</div></li>
        <li><span class="ico"><svg width="10" height="10" viewBox="0 0 10 10"><path d="M1.5 5.2 4 7.5 8.5 2.5" stroke="#fff" stroke-width="1.6" fill="none"/></svg></span><div><b>Friendly Care</b>A warm, welcoming clinic where every client feels at ease from day one.</div></li>
      </ul>
    </div>
    <div class="request">Request a Consultation — (03) 5550 2140</div>
  </article>
</section>

</body>
</html>
```